Travel Agency Website - Simple General

Need a 7 page simple design that is pretty repetitive. Need to be able to load quickly that is SEO optimized. Trying to give ideas on what they can do, be personal as we are local, but at the same time come across as professional and get information easily with little burden.

- Landing Page
- Brimwell Vacations Page
- Family Trips
- Road Trips from Texas
- Other Destinations
- About Us Page
- Contact Us Page

Target Market(s)

Families

Coding

Coded - Design and coding required

Number of Pages Required

5+ page

Colors

Designer to choose colors to be used in the design.

Requirements
Must have
• Like it to flow easily with our logo. Use that for colors, etc.

```html
<!DOCTYPE html>
<html lang="en">
<head>
<meta charset="utf-8">
<title>Wayfare Lane Travel Co.</title>
<link href="https://fonts.googleapis.com/css2?family=Oswald:wght@500;600;700&family=Poppins:wght@400;500&display=swap" rel="stylesheet">
<style>
:root{
  --cream:#fcf8f2;
  --navy:#0b3a4f;
  --teal:#2f8a86;
  --gold:#c9974a;
  --ink:#0c3347;
  --white:#ffffff;
}
*{margin:0;padding:0;box-sizing:border-box}
html,body{width:1200px;height:1089px;overflow:hidden}
body{position:relative;background:var(--cream);font-family:'Poppins',sans-serif;color:var(--ink)}
.hero-backdrop{position:absolute;left:0;top:0;width:1200px;height:520px;
  background:linear-gradient(90deg,#e9ede3 0%,#efe8dc 30%,#f1e2d3 55%,#efe6d8 80%,#ece5d6 100%);opacity:.75;
  -webkit-mask:linear-gradient(#000 55%,transparent);mask:linear-gradient(#000 55%,transparent)}
.brand{position:absolute;left:151px;top:30px;display:flex;align-items:center;gap:8px}
.brand-dot{width:22px;height:22px;border-radius:50%;background:var(--teal)}
.brand-name{font-family:'Oswald',sans-serif;font-weight:600;font-size:22px;color:var(--ink);letter-spacing:.5px;white-space:nowrap}
.main-nav{position:absolute;right:150px;top:35px;display:flex;align-items:center;gap:22px;font-size:10.5px;font-weight:500;letter-spacing:.2px}
.main-nav a{color:var(--ink);text-decoration:none}
.hero-title{position:absolute;left:0;width:1200px;top:142px;text-align:center;font-family:'Oswald',sans-serif;font-weight:700;font-size:47px;line-height:49px;color:var(--ink);letter-spacing:.5px}
.hero-title .accent{color:var(--teal)}
.cards{position:absolute;left:151px;top:330px;display:flex;gap:4px}
.card{width:222px}
.card-photo{width:222px;height:345px}
.card-title{margin-top:15px;font-family:'Oswald',sans-serif;font-weight:600;font-size:20.5px;line-height:23px;color:var(--ink)}
.card-note{font-size:9px;color:var(--ink);margin-top:1px}
.site-footer{position:absolute;left:0;top:800px;width:1200px;height:289px}
.footer-wave{position:absolute;left:0;top:0}
.footer-contact{position:absolute;left:151px;top:145px;font-size:12px;color:var(--white);line-height:20px}
.footer-contact li{list-style:none;display:flex;align-items:center;gap:7px}
.icon-badge{width:18px;height:18px;border-radius:50%;background:var(--gold);display:flex;align-items:center;justify-content:center}
.footer-brand{position:absolute;left:500px;top:128px;width:200px;text-align:center}
.footer-brand .brand-dot{display:block;margin:0 auto 6px;background:var(--gold)}
.footer-brand .brand-name{color:var(--white)}
.social{position:absolute;left:985px;top:146px;display:flex;gap:4px}
.social span{width:30px;height:30px;border-radius:50%;background:var(--gold);display:block}
.footer-rule{position:absolute;left:150px;top:245px;width:900px;height:1px;background:rgba(255,255,255,.18)}
.copyright{position:absolute;left:0;width:1200px;top:259px;text-align:center;font-size:10.5px;color:var(--white)}
.to-top{position:absolute;left:1101px;top:231px;width:28px;height:28px;border-radius:50%;background:var(--teal);display:flex;align-items:center;justify-content:center}
</style>
</head>
<body>
<div class="hero-backdrop" role="img" aria-label="Faded collage of travellers at a beach, canyon and ancient pyramid"></div>

<header>
  <div class="brand"><span class="brand-dot"></span><span class="brand-name">Wayfare Lane</span></div>
  <nav class="main-nav">
    <svg width="12" height="11" viewBox="0 0 12 11" aria-label="Home"><path d="M6 0 0 5.5h1.6V11h3.2V7.5h2.4V11h3.2V5.5H12z" fill="#c9974a"/></svg>
    <a href="#">BRIMWELL VACATIONS</a>
    <a href="#">FAMILY TRIPS</a>
    <a href="#">TEXAS ROAD TRIPS</a>
    <a href="#">OTHER DESTINATIONS</a>
    <a href="#">ABOUT US</a>
    <a href="#">CONTACT US</a>
  </nav>
</header>

<h1 class="hero-title">WELCOME TO THE<br>WAYFARE <span class="accent">LANE</span></h1>

<section class="cards">
  <article class="card"><div class="card-photo" role="img" aria-label="Aerial sunset view of a small tropical island" style="background:linear-gradient(#f2a07a,#e88e8a 30%,#3fa7c4 60%,#0f5f8a)"></div><h2 class="card-title">BRIMWELL VACATIONS<br>LAND AND SEA</h2></article>
  <article class="card"><div class="card-photo" role="img" aria-label="Family posing on a rocky coastal cliff" style="background:linear-gradient(#6fb2e0,#4f8a3a 25%,#b49a5a 60%,#e8c98e)"></div><h2 class="card-title">FAMILY<br>TRIPS</h2></article>
  <article class="card"><div class="card-photo" role="img" aria-label="Couple standing on a jeep on a desert road at sunset" style="background:linear-gradient(#f5b86a,#e48a3c 45%,#a8501e 80%,#7a3a18)"></div><h2 class="card-title" style="margin-top:19px">TEXAS ROAD TRIPS</h2><p class="card-note">(Partnership with Pinecrest Van Rentals)</p></article>
  <article class="card"><div class="card-photo" role="img" aria-label="Traveller with camera beside an ancient stone temple" style="background:linear-gradient(#6aa7d8,#d8dde0 35%,#a48a78 65%,#6d5a4c)"></div><h2 class="card-title">OTHER<br>DESTINATIONS</h2></article>
</section>

<footer class="site-footer">
  <svg class="footer-wave" width="1200" height="289" viewBox="0 0 1200 289" aria-hidden="true">
    <path d="M0 108C160 62 360 64 480 62 540 58 570 30 600 8 630 30 660 58 720 62 840 64 1040 62 1200 108V289H0z" fill="#0b3a4f"/>
    <path d="M0 100C160 54 360 56 480 54 540 50 570 22 600 0 630 22 660 50 720 54 840 56 1040 54 1200 100" fill="none" stroke="#2f8a86" stroke-width="1.5"/>
  </svg>
  <ul class="footer-contact">
    <li><span class="icon-badge"><svg width="9" height="9" viewBox="0 0 10 10"><path d="M2 0l2 2.5-1 1.3a6 6 0 0 0 3.2 3.2L7.5 6 10 8 8.6 9.8C4 9.6.4 6 .2 1.4z" fill="#fff"/></svg></span>555.010.2040</li>
    <li><span class="icon-badge"><svg width="9" height="7" viewBox="0 0 10 7"><rect width="10" height="7" rx="1" fill="#fff"/><path d="M0 .5 5 4l5-3.5" fill="none" stroke="#c9974a"/></svg></span>hello@wayfarelane.com</li>
  </ul>
  <div class="footer-brand"><span class="brand-dot"></span><span class="brand-name">Wayfare Lane</span></div>
  <div class="social"><span aria-label="Social profile one"></span><span aria-label="Social profile two"></span></div>
  <div class="footer-rule"></div>
  <p class="copyright">© 2026 WayfareLane / All Rights Reserved</p>
  <a class="to-top" href="#" aria-label="Back to top"><svg width="8" height="5" viewBox="0 0 8 5"><path d="M1 4l3-3 3 3" fill="none" stroke="#fff" stroke-width="1.4"/></svg></a>
</footer>
</body>
</html>
```